Meadowlark Property Review is a leading provider of residential appraisal and home inspection products in S

I need a business card/logo designed that obviously describes my business. We are a residential appraisal and home inspection company in Springfield, MO. We offer residential appraisals, home inspection, pest inspection and radon gas measurement. We have been in business for 18 years and hold state certified residential appraisal licenses and OBREX certified home inspection licenses. I have a logo that I really like and will attach, but would be open to new suggestions. I like more modern designs than traditional and would like a two sided card with our services, licenses and qualifications on the back.

```html
<!DOCTYPE html>
<html lang="en">
<head>
<meta charset="utf-8">
<title>Meadowlark Property Review — Business Card</title>
<link rel="stylesheet" href="https://fonts.googleapis.com/css2?family=Open+Sans:ital,wght@0,400;0,600;1,400&display=swap">
<style>
  :root {
    --stage: #3b3b3b;
    --paper: #f7f7f7;
    --brown: #8c6a40;
    --orange: #ef8a1e;
    --ink: #3d3d3d;
    --icon: #6b6b6b;
  }
  * { margin: 0; padding: 0; box-sizing: border-box; }
  html, body { width: 1200px; height: 750px; overflow: hidden; }
  body {
    background: var(--stage);
    font-family: "Open Sans", Arial, sans-serif;
    position: relative;
  }
  .card {
    position: absolute;
    top: 228px;
    width: 462px;
    height: 263px;
    background: var(--paper);
    overflow: hidden;
  }
  .card--front { left: 146px; }
  .card--back { left: 618px; }
  .card__band { position: absolute; inset: 0; width: 100%; height: 100%; }

  .contact { position: absolute; left: 29px; top: 22px; color: var(--ink); }
  .contact__name { font-size: 16.5px; font-weight: 600; color: var(--brown); line-height: 1.2; }
  .contact__role { font-size: 12.5px; color: var(--orange); line-height: 1.3; margin-bottom: 7px; }
  .contact__address { font-size: 11px; line-height: 14px; margin-bottom: 8px; }
  .contact__lines { list-style: none; font-size: 11px; }
  .contact__lines li { display: flex; align-items: center; height: 17.6px; }
  .contact__lines svg { width: 12px; height: 12px; margin-right: 6px; flex: none; fill: var(--icon); }
  .services { list-style: none; margin-top: 8px; font-size: 11.5px; font-style: italic; }
  .services li { position: relative; padding-left: 13px; line-height: 15px; }
  .services li::before {
    content: ""; position: absolute; left: 0; top: 6px;
    width: 4px; height: 4px; border-radius: 50%; background: var(--orange);
  }

  .brand {
    position: absolute; left: 200px; top: 98px; width: 240px;
    display: flex; align-items: center; justify-content: center; gap: 8px;
  }
  .brand__mark { width: 12px; height: 12px; background: var(--orange); flex: none; }
  .brand__name {
    font-size: 17px; font-weight: 600; color: var(--brown);
    line-height: 1.15; white-space: nowrap;
  }
</style>
</head>
<body>
  <section class="card card--front">
    <svg class="card__band" viewBox="0 0 462 263" aria-hidden="true">
      <polygon points="462,0 462,101 294,263 193,263" fill="var(--brown)"/>
    </svg>
    <div class="contact">
      <p class="contact__name">Daniel Harper</p>
      <p class="contact__role">CEO/Founder</p>
      <p class="contact__address">412 Larkspur Court<br>Cedar Hollow, Missouri 65810</p>
      <ul class="contact__lines">
        <li><svg viewBox="0 0 24 24"><path d="M6.6 10.8a15.1 15.1 0 0 0 6.6 6.6l2.2-2.2c.3-.3.7-.4 1-.2 1.1.4 2.3.6 3.6.6.6 0 1 .4 1 1V20c0 .6-.4 1-1 1A17 17 0 0 1 3 4c0-.6.4-1 1-1h3.5c.6 0 1 .4 1 1 0 1.3.2 2.5.6 3.6.1.3 0 .7-.2 1z"/></svg>417 555 0182</li>
        <li><svg viewBox="0 0 24 24"><path d="M6 2h12v6H6zM3 9h18a1 1 0 0 1 1 1v7h-4v4H6v-4H2v-7a1 1 0 0 1 1-1zm5 7v3h8v-3z"/></svg>417 555 0196</li>
        <li><svg viewBox="0 0 24 24"><path d="M2 5h20v14H2zm2 2v.5l8 5 8-5V7zm0 3v7h16v-7l-8 5z"/></svg>daniel@meadowlarkreview.com</li>
        <li><svg viewBox="0 0 24 24"><path d="M12 2a10 10 0 1 0 0 20 10 10 0 0 0 0-20zm-1 17.9A8 8 0 0 1 4.2 10L9 15v1a2 2 0 0 0 2 2zm6.9-2.5A2 2 0 0 0 16 16h-1v-3a1 1 0 0 0-1-1H8v-2h2a1 1 0 0 0 1-1V7h2a2 2 0 0 0 2-2v-.4a8 8 0 0 1 2.9 12.8z"/></svg>www.meadowlarkreview.com</li>
      </ul>
      <ul class="services">
        <li>Residential appraisals</li>
        <li>Home inspection</li>
        <li>Pest inspection and</li>
        <li>radon gas measurement.</li>
      </ul>
    </div>
  </section>

  <section class="card card--back">
    <svg class="card__band" viewBox="0 0 462 263" aria-hidden="true">
      <polygon points="0,0 269,263 166,263 0,100" fill="var(--orange)"/>
    </svg>
    <div class="brand">
      <span class="brand__mark"></span>
      <span class="brand__name">Meadowlark<br>Property Review</span>
    </div>
  </section>
</body>
</html>
```